​Silver Harbor Rhythm provides personal, friendly service in a fun and high energy environment. We are based in Vermont.

We would like a card that appeals to a wide range of audiences as we do a wide range of events. Please feel free to check out our website silverharborrhythm.net for inspiration.

Target Market(s)

weddings, corporate, birthday parties, colleges

Industry/Entity Type

Business

Contact Information for Business Card

Silver Harbor Rhythm
Providing Entertainment For All Occasions
555 274 9160
silverharborrhythm@mailnest.net
silverharborrhythm.net

```html
<!DOCTYPE html>
<html lang="en">
<head>
<meta charset="utf-8">
<title>Silver Harbor Rhythm – Business Card</title>
<link rel="stylesheet" href="https://fonts.googleapis.com/css2?family=Open+Sans:wght@400;600;700&display=swap">
<style>
  :root {
    --backdrop: #e9e7e3;
    --card: #ffffff;
    --forest: #2f5a1c;
    --forest-light: #4f7d35;
    --ink: #3b3b3b;
    --muted: #5a5a5a;
    --on-forest: #ffffff;
  }
  * { box-sizing: border-box; margin: 0; padding: 0; }
  html, body {
    width: 1200px; height: 1200px; overflow: hidden;
    background: var(--backdrop);
    font-family: "Open Sans", Arial, sans-serif;
    color: var(--ink);
  }
  .canvas { position: relative; width: 1200px; height: 1200px; }
  .card {
    position: absolute; left: 150px;
    width: 900px; height: 514px;
    background: var(--card);
    border-radius: 34px;
    overflow: hidden;
    box-shadow: 0 6px 22px rgba(0,0,0,0.12);
  }
  .card--front { top: 58px; }
  .card--back { top: 630px; }

  .wave { position: absolute; inset: 0; width: 100%; height: 100%; }

  .brand {
    position: absolute;
    display: flex; align-items: center; gap: 14px;
    color: var(--forest);
    font-weight: 700;
    letter-spacing: 0.5px;
    white-space: nowrap;
  }
  .brand__mark { display: block; width: 22px; height: 22px; background: var(--forest); }
  .card--front .brand { left: 112px; top: 160px; font-size: 38px; }
  .card--back .brand {
    left: 0; right: 0; top: 190px; justify-content: center; font-size: 56px;
  }
  .card--back .brand__mark { width: 30px; height: 30px; }

  .person { position: absolute; right: 66px; top: 168px; text-align: right; }
  .person__name { font-size: 27px; font-weight: 700; color: var(--forest); }
  .person__title { font-size: 22px; color: var(--ink); margin-top: 2px; }

  .contact {
    position: absolute; left: 112px; top: 290px;
    list-style: none; font-size: 20px; color: var(--ink);
  }
  .contact li { display: flex; align-items: center; gap: 10px; line-height: 34px; }
  .contact svg { width: 18px; height: 18px; flex: none; }

  .address {
    position: absolute; right: 52px; top: 410px; text-align: right;
    color: var(--on-forest); font-size: 20px; line-height: 40px; font-style: normal;
  }

  .site {
    position: absolute; left: 0; right: 0; top: 318px; text-align: center;
    font-size: 30px; color: var(--muted); letter-spacing: 0.5px;
  }
</style>
</head>
<body>
<main class="canvas">

  <section class="card card--front" aria-label="Business card front">
    <svg class="wave" viewBox="0 0 900 514" preserveAspectRatio="none" aria-hidden="true">
      <path d="M0,450 C250,520 560,420 900,320 L900,514 L0,514 Z" fill="var(--forest)"/>
      <path d="M0,462 C250,532 560,432 900,334" fill="none" stroke="var(--forest-light)" stroke-width="6" opacity="0.6"/>
      <path d="M60,490 C300,520 580,440 900,348" fill="none" stroke="#ffffff" stroke-width="4"/>
    </svg>

    <div class="brand"><span class="brand__mark"></span>Silver Harbor Rhythm</div>

    <div class="person">
      <p class="person__name">Your Name</p>
      <p class="person__title">Title</p>
    </div>

    <ul class="contact">
      <li>
        <svg viewBox="0 0 18 18" aria-hidden="true"><circle cx="9" cy="9" r="9" fill="var(--ink)"/><path d="M6,4.5 L8,6.5 L7,8 Q8.5,10.5 10,11 L11.5,10 L13.5,12 L12,13.5 Q7,13 4.5,6 Z" fill="#fff"/></svg>
        555 274 9160
      </li>
      <li>
        <svg viewBox="0 0 18 18" aria-hidden="true"><circle cx="9" cy="9" r="9" fill="var(--ink)"/><rect x="4.5" y="6" width="9" height="6.5" fill="#fff"/><path d="M4.5,6 L9,10 L13.5,6" fill="none" stroke="var(--ink)" stroke-width="1"/></svg>
        silverharborrhythm@mailnest.net
      </li>
      <li>
        <svg viewBox="0 0 18 18" aria-hidden="true"><circle cx="9" cy="9" r="9" fill="var(--ink)"/><circle cx="9" cy="9" r="4.5" fill="none" stroke="#fff" stroke-width="1.2"/><path d="M4.5,9 H13.5 M9,4.5 V13.5" stroke="#fff" stroke-width="1"/></svg>
        www.silverharborrhythm.net
      </li>
    </ul>

    <address class="address">
      Sreet Name, City Name<br>
      Zip Code-00000
    </address>
  </section>

  <section class="card card--back" aria-label="Business card back">
    <div class="brand"><span class="brand__mark"></span>Silver Harbor Rhythm</div>
    <p class="site">www.silverharborrhythm.net</p>
  </section>

</main>
</body>
</html>
```